Casino with the 'highest winning percentage' needs a stationery design

This is for a casino in Colombo, Sri Lanka and we need a stationery design for business card, letter head and envelope.

Should be very professional, simple and elegant without fancy fonts

Reason: Not fully satisfied with the designs. Need more designs.

Business

• 1. card deck symbol 'CLUBS' in red, or black

2. name in BLOCK CAPITAL LETTERS

3. Preferred font colours are black, white or red

4. Prefer 'professional /elegant' fonts
• SHOULD NOT HAVE ANY OTHER SYMBOL EXCEPT 'CLUBS'

DO NOT PREFER ITALIC FONTS

```html
<!DOCTYPE html>
<html lang="en">
<head>
<meta charset="utf-8">
<title>Harbourlight – Envelope</title>
<link rel="stylesheet" href="https://fonts.googleapis.com/css2?family=Montserrat:wght@400;600&display=swap">
<style>
  :root {
    --backdrop: #8f8f8f;
    --paper: #f4f4f4;
    --ink: #1e1e1e;
    --ink-soft: #3a3a3a;
    --accent-red: #c8161d;
  }
  * { margin: 0; padding: 0; box-sizing: border-box; }
  html, body {
    width: 1200px;
    height: 720px;
    overflow: hidden;
    background: var(--backdrop);
    font-family: "Montserrat", Arial, sans-serif;
  }
  .canvas {
    width: 1200px;
    height: 720px;
    display: flex;
    align-items: center;
    justify-content: center;
  }
  .envelope {
    position: relative;
    width: 1000px;
    height: 476px;
    background: var(--paper);
    box-shadow: 0 6px 22px rgba(0, 0, 0, 0.25);
  }
  .brand {
    position: absolute;
    top: 48px;
    left: 48px;
    display: flex;
    align-items: center;
    gap: 12px;
  }
  .brand-square {
    width: 14px;
    height: 14px;
    background: var(--ink);
    flex-shrink: 0;
  }
  .brand-name {
    font-size: 22px;
    font-weight: 600;
    line-height: 1;
    letter-spacing: 0.12em;
    color: var(--ink);
    text-transform: uppercase;
    white-space: nowrap;
  }
  .return-address {
    position: absolute;
    left: 48px;
    bottom: 40px;
    font-size: 12px;
    line-height: 1.35;
    color: var(--ink-soft);
    font-style: normal;
  }
  .return-address .website {
    display: block;
    margin-top: 10px;
    font-weight: 600;
    color: var(--accent-red);
  }
</style>
</head>
<body>
  <main class="canvas">
    <section class="envelope" aria-label="Business envelope">
      <header class="brand">
        <span class="brand-square" aria-hidden="true"></span>
        <span class="brand-name">Harbourlight</span>
      </header>
      <address class="return-address">
        HARBOURLIGHT LIMITED<br>
        18, Harbour View Mawatha<br>
        Colombo 01000, Sri Lanka
        <span class="website">www.harbourlightcolombo.com</span>
      </address>
    </section>
  </main>
</body>
</html>
```